Mara Penrith Copywriter Website

I am starting a new business as a freelance copywriter. Trying to set up the website for my business is proving to be too technical for me. I would like a simple, clean website using primarily black and white. I have attached the logo I would like used. I would like the menu icons to be Home, Services, Portfolio, Blog, Contact. I would like my mobile phone number (0412 583 906) and email address (mara.penrith.copywriter@fernmail.test) used in the header of the site. I need the site to be easily manageable and inter-changeable for me to be able to move things around and add images, etc with ease.

I would like the home page to be a static page with space for an image of myself somewhere (I haven't had this taken as yet), an area to put a bit about myself and my business, and also somewhere to include social media icons/links. Again, I would like the whole website and home page to be easily managed so that I can add/delete things with ease.

I would like the image of the typewriter used in the website somewhere also please.

Coding

Coded - Design and coding required

Number of Pages Required

5+ page

Font styles to use
Sans Serif
Script

Colors
fdf0f6

Requirements
Must have
• The logo provided
• Ability to change page contents easily
• Ability to add social media icons as needed
Nice to have
• Use of the typewriter image
Should not have
• Complicated pages that are not easily editable

```html
<!DOCTYPE html>
<html lang="en">
<head>
<meta charset="utf-8">
<title>Mara Penrith Copywriter</title>
<link href="https://fonts.googleapis.com/css2?family=Raleway:wght@700;800&family=Roboto:wght@300;400;500;700&family=Lato:wght@400;700&display=swap" rel="stylesheet">
<style>
:root{
  --ink:#111111;
  --black:#000000;
  --white:#ffffff;
  --blush:#fdf0f6;
  --grey-bg:#efefef;
  --text-grey:#777777;
  --footer:#1a1a1a;
  --footer-bar:#0b0b0b;
  --field:#3a3a3a;
}
*{margin:0;padding:0;box-sizing:border-box}
html,body{width:1200px;height:3285px;overflow:hidden}
body{position:relative;background:var(--white);font-family:"Lato",sans-serif;color:var(--ink)}
.abs{position:absolute}
section,header,footer{position:absolute;left:0;width:1200px}

/* header + hero */
.hero{top:0;height:679px;background:linear-gradient(120deg,#6f6f6f 0%,#b9b6b0 45%,#8c8780 70%,#4b4a46 100%)}
.topbar{top:0;height:94px;background:rgba(20,20,20,.82);z-index:2}
.brand{left:77px;top:30px;font-family:"Lato",sans-serif;font-weight:700;font-size:22px;color:var(--blush);letter-spacing:.5px}
.nav{left:462px;top:37px;display:flex;gap:30px;font-family:"Roboto",sans-serif;font-size:15px;color:#ddd;text-transform:uppercase}
.nav .active{color:var(--white);font-weight:500}
.call{left:922px;top:22px;display:flex;gap:14px;color:var(--white)}
.call small{display:block;font-family:"Roboto",sans-serif;font-size:13px}
.call strong{display:block;font-family:"Roboto",sans-serif;font-size:26px;font-weight:700}
.hero-title{left:77px;top:268px;font-family:"Raleway",sans-serif;font-weight:800;color:var(--white);text-transform:uppercase;line-height:1.08}
.hero-title .l1{font-size:56px;color:var(--blush)}
.hero-title .l2{font-size:64px}
.hero-title .l3{font-size:52px;color:var(--blush)}

/* welcome */
.welcome{top:679px;height:574px;background:var(--white)}
.welcome-photo{left:867px;top:0;width:333px;height:574px;background:linear-gradient(160deg,#3a3a3a,#111 70%)}
.typewriter{left:690px;top:76px;width:300px;height:420px;border-radius:10px;background:linear-gradient(180deg,#f2f2f2 0%,#e4e4e4 22%,#2a2a2a 23%,#161616 60%,#3a3a3a 100%)}
.kicker{font-family:"Roboto",sans-serif;font-weight:700;font-size:22px;text-transform:uppercase}
.heading{font-family:"Roboto",sans-serif;font-weight:300;font-size:40px;text-transform:uppercase;letter-spacing:.5px;white-space:nowrap}
.body-copy{font-size:14px;line-height:27px;color:var(--text-grey)}
.btn{display:inline-flex;align-items:center;justify-content:center;background:var(--black);color:var(--white);border-radius:30px;font-family:"Roboto",sans-serif;font-size:17px;text-transform:uppercase}

/* services */
.services{top:1253px;height:468px;background:var(--grey-bg)}
.service{width:300px;text-align:center}
.service .icon{width:104px;height:104px;border-radius:50%;background:var(--black);margin:0 auto;display:flex;align-items:center;justify-content:center}
.service h3{margin-top:30px;font-family:"Roboto",sans-serif;font-weight:700;font-size:20px}
.service p{margin-top:12px;font-size:13.5px;line-height:26px;color:var(--text-grey)}

/* portfolio */
.portfolio{top:1721px;height:769px;background:var(--white)}
.grid{left:77px;top:173px;display:grid;grid-template-columns:repeat(3,333px);grid-auto-rows:219px;gap:24px 24px}
.tile{display:block}

/* contact */
.contact{top:2490px;height:475px;background:linear-gradient(180deg,#f2f0ee,#e5e1dc 60%,#eceae6)}
.info-item{left:147px;display:flex;gap:18px;align-items:flex-start}
.info-item .dot{width:48px;height:48px;border-radius:50%;background:var(--black);display:flex;align-items:center;justify-content:center;flex:none}
.info-item b{display:block;font-size:14px;margin-top:4px}
.info-item span{display:block;font-size:13.5px;color:#555;margin-top:4px}
.field{background:var(--white);font-size:13px;color:#777;padding:14px 14px}

/* footer */
.footer{top:2965px;height:259px;background:var(--footer);color:#bbb}
.footer h4{font-family:"Roboto",sans-serif;font-weight:700;font-size:15px;color:var(--white);text-transform:uppercase}
.sitemap li{list-style:none;font-size:13px;line-height:28px}
.sitemap li::before{content:"";display:inline-block;width:6px;height:6px;border-radius:50%;background:var(--white);margin-right:12px;vertical-align:middle}
.input{width:248px;height:38px;background:var(--field);font-size:11px;color:#aaa;padding:12px}
.social{width:44px;height:44px;border-radius:50%;background:var(--white);display:flex;align-items:center;justify-content:center}
.copyright{top:3224px;height:61px;background:var(--footer-bar);color:#ccc;font-size:13px;text-align:center;line-height:61px}
</style>
</head>
<body>

<section class="hero">
  <div class="abs" style="left:0;top:0;width:1200px;height:679px" role="img" aria-label="Photograph of a woman thinking at her desk"></div>
  <h1 class="abs hero-title"><span class="l1">Ready to</span><br><span class="l2">Freelance as a</span><br><span class="l3">Copywriter</span></h1>
  <svg class="abs" style="left:90px;top:468px" width="270" height="140" viewBox="0 0 270 140">
    <polyline points="4,0 4,132 212,132" fill="none" stroke="#fff" stroke-width="2"/>
    <circle cx="238" cy="106" r="26" fill="none" stroke="#fff" stroke-width="4"/>
    <polygon points="230,95 230,117 248,106" fill="#fff"/>
  </svg>
</section>

<header class="topbar">
  <div class="abs brand">Mara Penrith Copywriter</div>
  <nav class="abs nav"><span class="active">Home</span><span>Services</span><span>Portfolio</span><span>Blog</span><span>Contact</span></nav>
  <div class="abs call">
    <svg width="36" height="40" viewBox="0 0 24 24"><path fill="#fff" d="M6.6 10.8a15.1 15.1 0 0 0 6.6 6.6l2.2-2.2c.3-.3.7-.4 1-.2 1.1.4 2.3.6 3.6.6.6 0 1 .4 1 1V20c0 .6-.4 1-1 1A17 17 0 0 1 3 4c0-.6.4-1 1-1h3.5c.6 0 1 .4 1 1 0 1.3.2 2.5.6 3.6.1.3 0 .7-.2 1z"/></svg>
    <div><small>Call Us Today :</small><strong>0412 583 906</strong></div>
  </div>
</header>

<section class="welcome">
  <div class="abs welcome-photo" role="img" aria-label="Dark photograph of a desk beside the typewriter"></div>
  <div class="abs typewriter" role="img" aria-label="Photograph of a black vintage typewriter with a sheet of paper"></div>
  <div class="abs kicker" style="left:77px;top:118px">Welcome to</div>
  <h2 class="abs heading" style="left:77px;top:154px">Mara Penrith Copywriter</h2>
  <p class="abs body-copy" style="left:77px;top:208px;width:560px">Lorem Ipsum is simply dummy text of the printing and typesetting industry. Lorem Ipsum has been the industry's standard dummy text ever since the 1500s, when an unknown printer took a galley of type and scrambled.</p>
  <p class="abs body-copy" style="left:77px;top:306px;width:560px">Lorem Ipsum is simply dummy text of the printing and typesetting industry. Lorem Ipsum has been the industry's standard dummy text ever since the 1500s, when an unknown printer took a galley of type and scrambled.</p>
  <a class="abs btn" style="left:77px;top:403px;width:181px;height:57px">Learn More</a>
</section>

<section class="services">
  <div class="abs kicker" style="left:80px;top:60px">What we do</div>
  <h2 class="abs heading" style="left:80px;top:96px">Our Services</h2>
  <svg class="abs" style="left:1010px;top:56px" width="116" height="58" viewBox="0 0 116 58">
    <circle cx="28" cy="29" r="26" fill="none" stroke="#333" stroke-width="1.5"/>
    <circle cx="86" cy="29" r="26" fill="none" stroke="#333" stroke-width="1.5"/>
    <path d="M40 29H16M23 22l-7 7 7 7" fill="none" stroke="#333" stroke-width="2"/>
    <path d="M74 29h24M91 22l7 7-7 7" fill="none" stroke="#333" stroke-width="2"/>
  </svg>
  <div class="abs service" style="left:84px;top:162px">
    <div class="icon"><svg width="56" height="50" viewBox="0 0 56 50"><rect x="2" y="2" width="52" height="46" rx="3" fill="none" stroke="#fff" stroke-width="4"/><line x1="2" y1="13" x2="54" y2="13" stroke="#fff" stroke-width="4"/><rect x="9" y="19" width="17" height="22" fill="#fff"/><rect x="31" y="19" width="16" height="9" fill="#fff"/><rect x="31" y="32" width="16" height="9" fill="#fff"/></svg></div>
    <h3>APP</h3>
    <p>Lorem Ipsum is simply dummy text of the printing and typesetting industry. Ipsum has been dummy text.</p>
  </div>
  <div class="abs service" style="left:446px;top:162px">
    <div class="icon"><svg width="60" height="50" viewBox="0 0 60 50"><path d="M16 22c0-12 6-18 14-18s14 6 14 18z" fill="#fff"/><rect x="8" y="21" width="44" height="4" rx="2" fill="#fff"/><path d="M14 34l14 6v-12zM46 34l-14 6v-12z" fill="#fff"/></svg></div>
    <h3>BRAND</h3>
    <p>Lorem Ipsum is simply dummy text of the printing and typesetting industry. Ipsum has been dummy text.</p>
  </div>
  <div class="abs service" style="left:802px;top:162px">
    <div class="icon"><svg width="56" height="56" viewBox="0 0 56 56"><circle cx="28" cy="28" r="20" fill="none" stroke="#fff" stroke-width="4"/><ellipse cx="28" cy="28" rx="8" ry="20" fill="none" stroke="#fff" stroke-width="3"/><line x1="8" y1="28" x2="48" y2="28" stroke="#fff" stroke-width="3"/><circle cx="8" cy="10" r="4" fill="#fff"/><circle cx="48" cy="10" r="4" fill="#fff"/><circle cx="8" cy="46" r="4" fill="#fff"/><circle cx="48" cy="46" r="4" fill="#fff"/></svg></div>
    <h3>SOCIAL</h3>
    <p>Lorem Ipsum is simply dummy text of the printing and typesetting industry. Ipsum has been dummy text.</p>
  </div>
</section>

<section class="portfolio">
  <div class="abs kicker" style="left:0;width:1200px;text-align:center;top:66px">Our Works</div>
  <h2 class="abs heading" style="left:0;width:1200px;text-align:center;top:102px">Our Portfolio</h2>
  <div class="abs grid">
    <div class="tile" style="background:linear-gradient(135deg,#2c2c2c,#4a4a4a);position:relative" role="img" aria-label="Photograph of hands on a laptop">
      <div style="position:absolute;inset:14px;border:1px solid rgba(255,255,255,.35)"></div>
      <svg style="position:absolute;left:148px;top:90px" width="40" height="40" viewBox="0 0 40 40"><circle cx="16" cy="16" r="12" fill="none" stroke="#fff" stroke-width="3"/><line x1="25" y1="25" x2="37" y2="37" stroke="#fff" stroke-width="4"/><path d="M16 10v12M10 16h12" stroke="#fff" stroke-width="3"/></svg>
    </div>
    <div class="tile" style="background:linear-gradient(135deg,#6b4a32,#3e2a1c)" role="img" aria-label="Photograph of a laptop, notes and coffee on a wooden table"></div>
    <div class="tile" style="background:linear-gradient(135deg,#d9d6d0,#9a958d)" role="img" aria-label="Photograph of hands typing on a tablet"></div>
    <div class="tile" style="background:linear-gradient(135deg,#3a3a3a,#7a5040 60%,#2a2a2a)" role="img" aria-label="Photograph of a red apple on a stack of books"></div>
    <div class="tile" style="background:linear-gradient(135deg,#cfc8be,#8e8478)" role="img" aria-label="Photograph of a person working on a laptop at a café table"></div>
    <div class="tile" style="background:linear-gradient(135deg,#8a8a8a,#2a2a2a)" role="img" aria-label="Black and white photograph of hands on a typewriter"></div>
  </div>
  <a class="abs btn" style="left:526px;top:651px;width:149px;height:57px">View All</a>
</section>

<section class="contact">
  <div class="abs" style="left:0;top:0;width:1200px;height:475px" role="img" aria-label="Faded photograph of a person writing outdoors"></div>
  <h2 class="abs heading" style="left:147px;top:60px"><b style="font-weight:700">Contact</b> Info</h2>
  <div class="abs info-item" style="top:136px">
    <div class="dot"><svg width="20" height="26" viewBox="0 0 20 26"><path d="M10 0a10 10 0 0 0-10 10c0 7 10 16 10 16s10-9 10-16A10 10 0 0 0 10 0z" fill="#fff"/><circle cx="10" cy="10" r="4" fill="#000"/></svg></div>
    <div><b>Address :</b><span>101 - Lorem ipsum simple print text</span></div>
  </div>
  <div class="abs info-item" style="top:204px">
    <div class="dot"><svg width="22" height="22" viewBox="0 0 24 24"><path fill="#fff" d="M6.6 10.8a15.1 15.1 0 0 0 6.6 6.6l2.2-2.2c.3-.3.7-.4 1-.2 1.1.4 2.3.6 3.6.6.6 0 1 .4 1 1V20c0 .6-.4 1-1 1A17 17 0 0 1 3 4c0-.6.4-1 1-1h3.5c.6 0 1 .4 1 1 0 1.3.2 2.5.6 3.6.1.3 0 .7-.2 1z"/></svg></div>
    <div><b>Phone :</b><span>0412 583 906</span></div>
  </div>
  <div class="abs info-item" style="top:272px">
    <div class="dot"><svg width="24" height="18" viewBox="0 0 24 18"><rect width="24" height="18" rx="2" fill="#fff"/><path d="M1 1l11 9 11-9" fill="none" stroke="#000" stroke-width="2"/></svg></div>
    <div><b>Email :</b><span>mara.penrith.copywriter@fernmail.test</span></div>
  </div>
  <div class="abs info-item" style="top:340px">
    <div class="dot"><svg width="22" height="22" viewBox="0 0 22 22"><rect x="5" y="1" width="12" height="6" fill="#fff"/><rect x="1" y="8" width="20" height="9" rx="2" fill="#fff"/><rect x="5" y="14" width="12" height="7" fill="#fff" stroke="#000" stroke-width="1.5"/></svg></div>
    <div><b>Fax :</b><span>123 4546 7890</span></div>
  </div>

  <h2 class="abs heading" style="left:585px;top:60px"><b style="font-weight:700">Contact</b> Us</h2>
  <div class="abs field" style="left:585px;top:142px;width:258px;height:48px">Name *</div>
  <div class="abs field" style="left:854px;top:142px;width:261px;height:48px">Phone *</div>
  <div class="abs field" style="left:585px;top:199px;width:258px;height:48px">Email *</div>
  <div class="abs field" style="left:854px;top:199px;width:261px;height:48px">Services *</div>
  <div class="abs field" style="left:585px;top:254px;width:530px;height:92px">Message *</div>
  <a class="abs btn" style="left:585px;top:357px;width:157px;height:52px">Submit</a>
</section>

<footer class="footer">
  <h4 class="abs" style="left:77px;top:38px">Mara Penrith Copywriter</h4>
  <p class="abs" style="left:77px;top:78px;width:250px;font-size:13px;line-height:27px">Lorem Ipsum is simply dummy text of the printing and typesetting industry. Ipsum has been dummy text.</p>
  <a class="abs" style="left:80px;top:164px;font-size:13px;font-weight:700;color:#fff;text-decoration:underline;font-style:italic">Read More...</a>
  <svg class="abs" style="left:163px;top:169px" width="14" height="10" viewBox="0 0 14 10"><path d="M1 1l4 4-4 4M7 1l4 4-4 4" fill="none" stroke="#fff" stroke-width="1.5"/></svg>

  <h4 class="abs" style="left:344px;top:38px">Sitemap</h4>
  <ul class="abs sitemap" style="left:344px;top:74px"><li>Home</li><li>Services</li><li>Portfolio</li><li>Blog</li><li>Contact</li></ul>

  <h4 class="abs" style="left:609px;top:38px">Newsletter</h4>
  <div class="abs input" style="left:609px;top:77px">Enter Email *</div>
  <div class="abs input" style="left:609px;top:122px">Enter Email *</div>
  <a class="abs btn" style="left:609px;top:171px;width:157px;height:47px;background:transparent;border:1.5px solid #fff;font-size:15px">Subscribe</a>

  <div class="abs" style="left:876px;top:84px;width:250px;font-family:'Lato',sans-serif;font-weight:700;font-size:19px;color:var(--blush)">Mara Penrith Copywriter</div>
  <a class="abs social" style="left:924px;top:142px" aria-label="Social link">
    <svg width="20" height="20" viewBox="0 0 20 20"><path d="M8 12l4-4M7 9l-2 2a3 3 0 0 0 4 4l2-2M13 11l2-2a3 3 0 0 0-4-4L9 7" fill="none" stroke="#000" stroke-width="2" stroke-linecap="round"/></svg>
  </a>
  <a class="abs social" style="left:977px;top:142px" aria-label="Social link">
    <svg width="20" height="20" viewBox="0 0 20 20"><circle cx="5" cy="10" r="2.5" fill="#000"/><circle cx="15" cy="4.5" r="2.5" fill="#000"/><circle cx="15" cy="15.5" r="2.5" fill="#000"/><path d="M5 10l10-5.5M5 10l10 5.5" stroke="#000" stroke-width="1.6"/></svg>
  </a>
  <a class="abs social" style="left:1029px;top:142px" aria-label="Social link">
    <svg width="20" height="20" viewBox="0 0 20 20"><rect x="2" y="4" width="16" height="12" rx="2" fill="#000"/><path d="M3 5l7 6 7-6" fill="none" stroke="#fff" stroke-width="1.5"/></svg>
  </a>
</footer>

<div class="abs copyright" style="left:0;width:1200px"><b style="color:#fff">©mara penrith copywriter</b> - 2018 All Right Reserved.</div>

</body>
</html>
```